Business Card Design

New business card design

Target Market(s)

Residential & Commercial Property Managers

Industry/Entity Type

Plumbing Services

Contact Information for Business Card

Name - Rowan Keddle, title - Director, Phone Number - 0431 286 517, email - rowan@tbk-plumbing.com.au, Company ABN - 73 215 904 386,

Font styles to use
Sans Serif

Colors
0054AA
0677BA
7BADD7
CADEEF
E8F1F8

```html
<!DOCTYPE html>
<html lang="en">
<head>
<meta charset="utf-8">
<title>TBK Plumbing Services – Business Card</title>
<link href="https://fonts.googleapis.com/css2?family=Michroma&family=Roboto+Condensed:wght@300;400&display=swap" rel="stylesheet">
<style>
  :root {
    --page-bg: #e6e8ea;
    --card-top: #f2eeee;
    --card-top-edge: #e2dcdc;
    --band-dark: #1f252b;
    --band-blue: #00aeef;
    --ink-dark: #1f252b;
    --ink-grey: #55595d;
    --ink-white: #ffffff;
  }
  html, body {
    margin: 0;
    width: 1200px;
    height: 900px;
    overflow: hidden;
    background: var(--page-bg);
  }
  .canvas {
    position: relative;
    width: 1200px;
    height: 900px;
  }
  .card {
    position: absolute;
    left: 100px;
    top: 140px;
    width: 1000px;
    height: 620px;
    overflow: hidden;
    box-shadow: 0 12px 36px rgba(0,0,0,0.18);
    font-family: "Roboto Condensed", sans-serif;
  }
  .card-face {
    position: absolute;
    left: 0; top: 0;
    width: 1000px;
    height: 392px;
    background: radial-gradient(ellipse at 50% 45%, var(--card-top) 40%, var(--card-top-edge) 100%);
  }
  .brand {
    position: absolute;
    left: 0; right: 0;
    top: 150px;
    display: flex;
    align-items: center;
    justify-content: center;
    gap: 18px;
  }
  .brand-dot {
    width: 22px;
    height: 22px;
    border-radius: 50%;
    background: var(--band-blue);
  }
  .brand-name {
    font-family: "Roboto Condensed", sans-serif;
    font-weight: 300;
    font-size: 56px;
    letter-spacing: 6px;
    color: var(--ink-dark);
  }
  .band {
    position: absolute;
    left: 0; top: 392px;
    width: 1000px;
    height: 228px;
    display: flex;
  }
  .band-details {
    position: relative;
    width: 560px;
    background: var(--band-dark);
  }
  .band-accent {
    position: relative;
    flex: 1;
    background: var(--band-blue);
  }
  .person-name {
    position: absolute;
    left: 38px; top: 28px;
    margin: 0;
    font-family: "Michroma", sans-serif;
    font-weight: 400;
    font-size: 31px;
    letter-spacing: 0.5px;
    color: var(--band-blue);
    text-transform: uppercase;
  }
  .person-title {
    position: absolute;
    left: 38px; top: 68px;
    margin: 0;
    font-size: 30px;
    color: var(--ink-white);
  }
  .contact-list {
    position: absolute;
    left: 38px; top: 128px;
    margin: 0; padding: 0;
    list-style: none;
  }
  .contact-item {
    display: flex;
    align-items: center;
    gap: 12px;
    height: 36px;
    font-size: 30px;
    color: var(--ink-white);
  }
  .contact-icon { width: 28px; height: 28px; flex: none; }
  .abn {
    position: absolute;
    right: 52px; bottom: 44px;
    margin: 0;
    font-size: 30px;
    color: var(--ink-white);
    word-spacing: 4px;
  }
</style>
</head>
<body>
<main class="canvas">
  <article class="card">
    <section class="card-face">
      <div class="brand">
        <span class="brand-dot"></span>
        <span class="brand-name">TBK Plumbing Services</span>
      </div>
    </section>
    <section class="band">
      <div class="band-details">
        <h1 class="person-name">Rowan Keddle</h1>
        <p class="person-title">Director</p>
        <ul class="contact-list">
          <li class="contact-item">
            <svg class="contact-icon" viewBox="0 0 24 24" aria-hidden="true">
              <path fill="#00aeef" d="M6.6 10.8a15.1 15.1 0 0 0 6.6 6.6l2.2-2.2a1 1 0 0 1 1-.25 11.4 11.4 0 0 0 3.6.57 1 1 0 0 1 1 1V20a1 1 0 0 1-1 1A17 17 0 0 1 3 4a1 1 0 0 1 1-1h3.5a1 1 0 0 1 1 1c0 1.25.2 2.45.57 3.57a1 1 0 0 1-.25 1z"/>
            </svg>
            <span>0431 286 517</span>
          </li>
          <li class="contact-item">
            <svg class="contact-icon" viewBox="0 0 24 24" aria-hidden="true">
              <rect x="2" y="5" width="20" height="14" fill="#00aeef"/>
              <path d="M2 5l10 8 10-8M2 19l7.5-7M22 19l-7.5-7" fill="none" stroke="#1f252b" stroke-width="1.4"/>
            </svg>
            <span>rowan@tbk-plumbing.com.au</span>
          </li>
        </ul>
      </div>
      <div class="band-accent">
        <p class="abn">ABN&nbsp; 73 215 904 386</p>
      </div>
    </section>
  </article>
</main>
</body>
</html>
```